KTWG application splash screen

We need a 1024x768 image for use as an application splash screen.
The image will be displayed full screen on an 10 inch industrial PC 1024x768 screen while our application is launching. The image should convey that the application is "Waiting for connection to Wi-Fi access point..." and include a graphic of the industrial PC connected to the access point via an Ethernet cable. A list of troubleshooting steps should be included at the bottom of the image. The troubleshooting steps should not be the main focus of the image and should be shown in a smaller font (but still readable at 1024x768 displayed on a 10 inch screen).
I will include a mock up of the general idea of what we are looking for as well as image files for the industrial PC, a screenshot of our application to show on the PC's screen and the AP.
For general look and feel and a sense of corporate branding please review our website https://marrowgatesoilworks.example/. The splash screen should reflect corporate branding.
Target Market(s)
Users of our application
Industry/Entity Type
Agriculture
Look and feel

```html
<!DOCTYPE html>
<html lang="en">
<head>
<meta charset="utf-8">
<title>KTWG – Waiting for Wi-Fi access point</title>
<link rel="stylesheet" href="https://fonts.googleapis.com/css2?family=Poppins:wght@300;400;500;600;700&display=swap">
<style>
  :root {
    --brand-green: #42bd6b;
    --title-green: #3db866;
    --white: #ffffff;
    --black: #000000;
    --device-dark: #2b2b2b;
    --device-screen: #e9ece9;
    --ap-white: #f3f4f4;
  }
  * { box-sizing: border-box; margin: 0; padding: 0; }
  html, body {
    width: 1200px; height: 1200px; overflow: hidden;
    background: var(--black);
    font-family: "Poppins", sans-serif;
  }
  .splash {
    position: absolute; left: 111px; top: 233px;
    width: 979px; height: 733px;
    background: var(--white);
  }
  .band { position: absolute; left: 0; width: 100%; background: var(--brand-green); }
  .band--top { top: 0; height: 197px; }
  .band--bottom { top: 547px; height: 186px; }

  .status-card {
    position: absolute; left: 283px; top: 0; width: 413px; height: 163px;
    background: var(--white);
    border-radius: 0 0 25px 25px;
    display: flex; align-items: center; justify-content: center;
  }
  .status-title {
    color: var(--title-green);
    font-weight: 600; font-size: 35px; line-height: 34px;
    letter-spacing: 1.5px; text-align: center;
    margin-top: 2px;
  }

  .node {
    position: absolute; top: 238px; width: 262px; height: 262px;
    border-radius: 50%; background: var(--brand-green);
  }
  .node--pc { left: 52px; }
  .node--ap { left: 665px; }
  .node-visual { position: absolute; }
  .node--pc .node-visual {
    left: 41px; top: 25px; width: 179px; height: 143px;
    border-radius: 10px;
    background: linear-gradient(var(--device-dark), var(--device-dark));
    border: 2px solid #dcdcdc;
  }
  .node--pc .node-visual::after {
    content: ""; position: absolute; left: 15px; top: 11px; right: 16px; bottom: 22px;
    background: var(--device-screen); border-radius: 2px;
  }
  .node--ap .node-visual {
    left: 121px; top: 23px; width: 19px; height: 147px;
    border-radius: 4px;
    background: linear-gradient(90deg, #e4e6e6, var(--ap-white), #e1e3e3);
  }
  .node-label {
    position: absolute; left: 0; width: 100%; text-align: center; color: var(--white);
  }
  .node-name { top: 181px; font-weight: 600; font-size: 18.5px; letter-spacing: 1px; line-height: 22px; }
  .node-sub { top: 203px; font-weight: 300; font-size: 14.5px; letter-spacing: 1px; line-height: 18px; }
  .node--ap .node-sub { font-size: 12px; letter-spacing: 1.2px; top: 205px; }

  .link-line { position: absolute; left: 335px; top: 366px; width: 310px; height: 10px; }
  .link-label {
    position: absolute; left: 300px; width: 380px; top: 383px;
    text-align: center; color: var(--title-green);
    font-weight: 600; font-size: 19.5px; letter-spacing: 1.5px;
  }

  .help-card {
    position: absolute; left: 276px; top: 579px; width: 426px; height: 154px;
    background: var(--white); border-radius: 19px 19px 0 0;
    color: var(--title-green);
  }
  .help-title {
    text-align: center; font-weight: 600; font-size: 14px; letter-spacing: 1.2px;
    margin-top: 11px; line-height: 18px;
  }
  .help-list { list-style: none; margin: 4px 0 0 28px; font-size: 10px; line-height: 11.5px; font-weight: 400; }
  .help-list li { position: relative; padding-left: 7px; }
  .help-list li::before { content: "•"; position: absolute; left: 0; }
  .help-list .help-list { margin: 0 0 0 12px; padding: 0; }

  .brand-mark {
    position: absolute; left: 855px; top: 615px; width: 90px; height: 90px;
    background: var(--black); border: 3px solid var(--white); border-radius: 20px;
    display: flex; align-items: center; justify-content: center;
    color: var(--white); font-weight: 700; font-size: 22px; letter-spacing: 1px;
  }
</style>
</head>
<body>
  <main class="splash">
    <div class="band band--top"></div>
    <div class="band band--bottom"></div>

    <header class="status-card">
      <h1 class="status-title">Waiting for<br>connection to Wi-Fi<br>access point...</h1>
    </header>

    <section class="node node--pc">
      <div class="node-visual" role="img" aria-label="Industrial tablet PC showing the KTWG application screen"></div>
      <div class="node-label node-name">TRACTOR CAB</div>
      <div class="node-label node-sub">COMPUTER</div>
    </section>

    <svg class="link-line" viewBox="0 0 310 10" aria-hidden="true">
      <g fill="#42bd6b">
        <circle cx="3" cy="5" r="2.6"/><circle cx="13.2" cy="5" r="2.6"/><circle cx="23.4" cy="5" r="2.6"/><circle cx="33.6" cy="5" r="2.6"/><circle cx="43.8" cy="5" r="2.6"/><circle cx="54" cy="5" r="2.6"/><circle cx="64.2" cy="5" r="2.6"/><circle cx="74.4" cy="5" r="2.6"/><circle cx="84.6" cy="5" r="2.6"/><circle cx="94.8" cy="5" r="2.6"/><circle cx="105" cy="5" r="2.6"/><circle cx="115.2" cy="5" r="2.6"/><circle cx="125.4" cy="5" r="2.6"/><circle cx="135.6" cy="5" r="2.6"/><circle cx="145.8" cy="5" r="2.6"/><circle cx="156" cy="5" r="2.6"/><circle cx="166.2" cy="5" r="2.6"/><circle cx="176.4" cy="5" r="2.6"/><circle cx="186.6" cy="5" r="2.6"/><circle cx="196.8" cy="5" r="2.6"/><circle cx="207" cy="5" r="2.6"/><circle cx="217.2" cy="5" r="2.6"/><circle cx="227.4" cy="5" r="2.6"/><circle cx="237.6" cy="5" r="2.6"/><circle cx="247.8" cy="5" r="2.6"/><circle cx="258" cy="5" r="2.6"/><circle cx="268.2" cy="5" r="2.6"/><circle cx="278.4" cy="5" r="2.6"/><circle cx="288.6" cy="5" r="2.6"/><circle cx="298.8" cy="5" r="2.6"/><circle cx="307" cy="5" r="2.6"/>
      </g>
    </svg>
    <div class="link-label">ETHERNET CABLE</div>

    <section class="node node--ap">
      <div class="node-visual" role="img" aria-label="White outdoor Wi-Fi access point with two antennas"></div>
      <div class="node-label node-name">WI-FI ACCESS POINT</div>
      <div class="node-label node-sub">NORVALE AP-220 OUTDOOR</div>
    </section>

    <section class="help-card">
      <h2 class="help-title">TROUBLESHOOTING STEPS:</h2>
      <ul class="help-list">
        <li>This screen should only be visible for a short time on boot.</li>
        <li>If this screen stays visible for more than a minute:
          <ul class="help-list">
            <li>Verify that the Wi-Fi Access Point (AP) powers up when this system does (indicated by a green light on the side of the AP).</li>
            <li>Check the Ethernet cable between this system and the AP for damage, and replace it if necessary.</li>
            <li>Power-cycle this system and wait for it to reboot fully.</li>
            <li>If the issue persists, contact KTWG support for further assistance.</li>
          </ul>
        </li>
      </ul>
    </section>

    <div class="brand-mark">KTWG</div>
  </main>
</body>
</html>
```